Business Card Design Project

I need a business card designed from scratch. I have an existing logo that I can upload in Illustrator for modification or redesign.

The Company is called Query Lanterns http://querylanterns.com.au and we provide Search Engine Optimization services to Australian businesses. The current logo signifies an increase in visitors, profits etc...

There are no restrictions as to the redesign - colours, style etc are all open to change.

Cards will be full colour and one sided printed at http://www.cardmoxel.com.au so check their requirements for file format and sizes etc.

I will expect all original files upon completion of project.

Target Market(s)

Any business with a web site looking to improve their search engine rankings

Industry/Entity Type

Business

Requirements
Must have
• I like modern, sleek designs. Clean, not fussy, uncluttered.

```html
<!DOCTYPE html>
<html lang="en">
<head>
<meta charset="utf-8">
<title>Query Lanterns — Business Card</title>
<link rel="stylesheet" href="https://fonts.googleapis.com/css2?family=Open+Sans:wght@400;600;800&display=swap">
<style>
  :root {
    --brand-blue: #2f6db3;
    --brand-blue-deep: #245a98;
    --brand-yellow: #f3b824;
    --card-white: #f6f7f9;
    --card-tint: #e9ecf0;
    --ink: #1c1f24;
    --ink-soft: #4a4f57;
    --backdrop: #d9d4cc;
  }
  * { box-sizing: border-box; margin: 0; padding: 0; }
  html, body {
    width: 1200px; height: 900px; overflow: hidden;
    background: var(--backdrop);
    font-family: "Open Sans", Arial, sans-serif;
  }
  .stage {
    width: 1200px; height: 900px;
    display: flex; align-items: center; justify-content: center; gap: 90px;
  }
  .card {
    position: relative;
    width: 340px; height: 560px;
    background: linear-gradient(160deg, var(--card-white), var(--card-tint));
    box-shadow: 0 14px 30px rgba(0,0,0,.18);
    overflow: hidden;
  }
  .wordmark {
    display: flex; align-items: center; gap: 8px;
    color: var(--brand-blue);
    font-weight: 800;
    line-height: 1;
    letter-spacing: -0.5px;
  }
  .wordmark__dot {
    width: 14px; height: 14px; border-radius: 50%;
    background: var(--brand-yellow);
    flex: none;
  }
  .card--front .wordmark {
    position: absolute; top: 62px; right: 28px;
    font-size: 27px;
  }
  .contact {
    position: absolute; left: 40px; top: 150px;
    color: var(--ink);
  }
  .contact__name {
    font-size: 19px; font-weight: 600; letter-spacing: .3px;
  }
  .contact__role {
    font-size: 10px; color: var(--ink-soft); margin-bottom: 12px;
  }
  .contact__list { list-style: none; }
  .contact__item {
    display: flex; align-items: center; gap: 8px;
    font-size: 12px; line-height: 20px; color: var(--ink);
  }
  .contact__item--web { font-size: 14px; }
  .contact__icon { width: 12px; height: 12px; flex: none; color: var(--brand-blue); }
  .accent-tab {
    position: absolute; left: 0; top: 152px;
    width: 8px; height: 34px; background: var(--brand-yellow);
  }
  .ribbon-art {
    position: absolute; left: 0; bottom: 0; width: 340px; height: 270px;
  }
  .card--back {
    display: flex; align-items: center; justify-content: center;
  }
  .card--back .wordmark { font-size: 34px; }
</style>
</head>
<body>
<main class="stage">
  <section class="card card--front" aria-label="Business card front">
    <div class="wordmark"><span class="wordmark__dot"></span>Query Lanterns</div>
    <span class="accent-tab"></span>
    <div class="contact">
      <p class="contact__name">NED HARLOW</p>
      <p class="contact__role">Owner</p>
      <ul class="contact__list">
        <li class="contact__item">
          <svg class="contact__icon" viewBox="0 0 24 24"><path fill="currentColor" d="M6.6 10.8a15 15 0 0 0 6.6 6.6l2.2-2.2a1 1 0 0 1 1-.25 11.4 11.4 0 0 0 3.6.57 1 1 0 0 1 1 1V20a1 1 0 0 1-1 1A17 17 0 0 1 3 4a1 1 0 0 1 1-1h3.5a1 1 0 0 1 1 1c0 1.25.2 2.45.57 3.57a1 1 0 0 1-.25 1z"/></svg>
          1300 555 018
        </li>
        <li class="contact__item">
          <svg class="contact__icon" viewBox="0 0 24 24"><path fill="none" stroke="currentColor" stroke-width="2" d="M3 6h18v12H3z M3 6l9 7 9-7"/></svg>
          enquiry@querylanterns.com.au
        </li>
        <li class="contact__item contact__item--web">
          <svg class="contact__icon" viewBox="0 0 24 24"><g fill="none" stroke="currentColor" stroke-width="2"><circle cx="12" cy="12" r="9"/><path d="M3 12h18M12 3c3 3.5 3 14.5 0 18M12 3c-3 3.5-3 14.5 0 18"/></g></svg>
          www.querylanterns.com.au
        </li>
      </ul>
    </div>
    <svg class="ribbon-art" viewBox="0 0 340 270" role="img" aria-label="Blue and yellow folded ribbon artwork rising like a growth graph">
      <defs>
        <linearGradient id="ribbon-fill" x1="0" y1="0" x2="0" y2="1">
          <stop offset="0" stop-color="#3a7bc2"/>
          <stop offset="1" stop-color="#245a98"/>
        </linearGradient>
      </defs>
      <path d="M0 40 L60 70 L120 150 L190 120 L260 30 L340 0 V270 H0 Z" fill="url(#ribbon-fill)"/>
    </svg>
  </section>

  <section class="card card--back" aria-label="Business card back">
    <div class="wordmark"><span class="wordmark__dot"></span>Query Lanterns</div>
  </section>
</main>
</body>
</html>
```